"Harbor Builders" is a residential building company and needs a new business card design and may re

We would like a redesign based on the existing logo, and would like to see a new font as well. We are bespoke home builders who build sustainable energy efficient homes.

Industry/Entity Type

Construction

Contact Information for Business Card

Business card size 40mm x 90mm

Colors

Designer to choose colors to be used in the design.

```html
<!DOCTYPE html>
<html lang="en">
<head>
<meta charset="utf-8">
<title>Harbor Builders – Business Card</title>
<link rel="stylesheet" href="https://fonts.googleapis.com/css2?family=Roboto:wght@400;500;700&family=Roboto+Condensed:wght@700&display=swap">
<style>
  :root {
    --lime: #b7d334;
    --ink: #1a1b1d;
    --paper: #f3f3f3;
    --muted: #444649;
    --stage: #e6e4e0;
  }
  * { box-sizing: border-box; margin: 0; padding: 0; }
  html, body {
    width: 1200px; height: 960px; overflow: hidden;
    background: var(--stage);
    font-family: "Roboto", Arial, sans-serif;
  }
  .canvas { position: relative; width: 1200px; height: 960px; }

  .card { position: absolute; box-shadow: 0 4px 10px rgba(0,0,0,.25); }

  /* Front */
  .card-front {
    left: 302px; top: 128px; width: 600px; height: 344px;
    background: var(--paper);
  }
  .brand {
    position: absolute; left: 50px; top: 92px;
    display: flex; align-items: center; gap: 14px;
  }
  .brand-square { width: 30px; height: 30px; background: var(--lime); }
  .brand-name {
    font-family: "Roboto", Arial, sans-serif; font-weight: 500;
    font-size: 30px; color: var(--ink); letter-spacing: -.3px;
  }
  .contact { position: absolute; left: 312px; top: 72px; }
  .contact-name {
    font-family: "Roboto Condensed", "Arial Narrow", sans-serif; font-weight: 700;
    font-size: 21px; color: var(--ink); margin-bottom: 22px;
  }
  .contact-list { list-style: none; }
  .contact-list li {
    display: flex; align-items: center; gap: 9px;
    font-size: 14.5px; color: var(--muted); line-height: 19px;
  }
  .contact-list svg { width: 13px; height: 13px; flex: none; }

  .band {
    position: absolute; left: 0; bottom: 0; width: 100%; height: 87px;
    background: var(--lime);
  }
  .address {
    position: absolute; left: 21px; top: 17px;
    font-size: 14px; line-height: 18px; color: var(--ink);
  }
  .address strong { font-weight: 700; }
  .registration {
    position: absolute; right: 21px; top: 23px; text-align: right;
    font-size: 14px; line-height: 18px; color: var(--ink);
  }
  .band-mark {
    position: absolute; left: 232px; top: -22px; width: 106px; height: 106px;
    background: var(--ink); border: 3px solid var(--paper);
  }

  /* Back */
  .card-back {
    left: 299px; top: 488px; width: 601px; height: 342px;
    background: var(--ink);
  }
  .back-brand {
    position: absolute; left: 0; top: 128px; width: 100%;
    display: flex; justify-content: center; align-items: center; gap: 18px;
  }
  .back-brand .brand-square { width: 44px; height: 44px; }
  .back-brand .brand-name { font-size: 44px; color: var(--lime); }
  .back-url {
    position: absolute; left: 0; top: 296px; width: 100%; text-align: center;
    font-size: 14px; letter-spacing: 2.6px; color: var(--lime);
  }
</style>
</head>
<body>
<main class="canvas">
  <section class="card card-front" aria-label="Business card front">
    <div class="brand">
      <span class="brand-square"></span>
      <span class="brand-name">harbor builders</span>
    </div>

    <div class="contact">
      <h1 class="contact-name">DANIEL MORETTI</h1>
      <ul class="contact-list">
        <li>
          <svg viewBox="0 0 13 13" aria-hidden="true"><rect x="3" y="0.5" width="7" height="12" rx="1.2" fill="none" stroke="#1a1b1d" stroke-width="1.5"/><rect x="5.5" y="10" width="2" height="1.2" fill="#1a1b1d"/></svg>
          0400 555 018
        </li>
        <li>
          <svg viewBox="0 0 13 13" aria-hidden="true"><rect x="0.5" y="2.5" width="12" height="8" fill="#1a1b1d"/><path d="M0.5 2.5 L6.5 7 L12.5 2.5" fill="none" stroke="#f3f3f3" stroke-width="1.2"/></svg>
          daniel@harborbuilders.com.au
        </li>
        <li>
          <svg viewBox="0 0 13 13" aria-hidden="true"><circle cx="6.5" cy="6.5" r="6" fill="#1a1b1d"/><path d="M0.5 6.5 H12.5 M6.5 0.5 C3.5 4 3.5 9 6.5 12.5 M6.5 0.5 C9.5 4 9.5 9 6.5 12.5" fill="none" stroke="#f3f3f3" stroke-width=".9"/></svg>
          www.harborbuilders.com.au
        </li>
      </ul>
    </div>

    <div class="band">
      <p class="address"><strong>Harbor Builders Pty Ltd</strong><br>PO Box 4120 Northgate<br>LPO Ridgeview WA 6099</p>
      <span class="band-mark"></span>
      <p class="registration">Registration 48310<br>ABN: 12 345 678 901</p>
    </div>
  </section>

  <section class="card card-back" aria-label="Business card back">
    <div class="back-brand">
      <span class="brand-square"></span>
      <span class="brand-name">harbor builders</span>
    </div>
    <p class="back-url">www.harborbuilders.com.au</p>
  </section>
</main>
</body>
</html>
```